​Silver Harbor Rhythm provides personal, friendly service in a fun and high energy environment. We are based in Vermont.

We would like a card that appeals to a wide range of audiences as we do a wide range of events. Please feel free to check out our website silverharborrhythm.net for inspiration.

Target Market(s)

weddings, corporate, birthday parties, colleges

Industry/Entity Type

Business

Contact Information for Business Card

Silver Harbor Rhythm
Providing Entertainment For All Occasions
555 274 9160
silverharborrhythm@mailnest.net
silverharborrhythm.net

```html
<!DOCTYPE html>
<html lang="en">
<head>
<meta charset="utf-8">
<title>Silver Harbor Rhythm — Business Card</title>
<link rel="stylesheet" href="https://fonts.googleapis.com/css2?family=Open+Sans:wght@400;600;700;800&display=swap">
<style>
  :root {
    --backdrop: #ecebe8;
    --card: #ffffff;
    --forest: #2f5a1a;
    --maroon: #4a1c22;
    --ink: #3a3a3a;
    --muted: #555555;
    --rule: #b9b9b9;
  }
  * { margin: 0; padding: 0; box-sizing: border-box; }
  html, body {
    width: 1200px; height: 829px; overflow: hidden;
    background: var(--backdrop);
    font-family: "Open Sans", Arial, sans-serif;
  }
  .canvas {
    position: relative; width: 1200px; height: 829px;
  }
  .card {
    position: absolute; top: 264px;
    width: 525px; height: 300px;
    background: var(--card);
    box-shadow: 0 2px 10px rgba(0,0,0,0.12);
    overflow: hidden;
  }
  .card--front { left: 50px; }
  .card--back { left: 625px; }

  .corner-bands { position: absolute; top: 0; left: 0; width: 525px; height: 110px; }
  .holder { position: absolute; top: 10px; right: 22px; text-align: right; color: #fff; }
  .holder__name { font-size: 13px; font-weight: 700; line-height: 1.2; }
  .holder__title { font-size: 10px; font-weight: 400; }

  .brand-name {
    color: var(--forest);
    font-weight: 800;
    text-transform: uppercase;
    letter-spacing: 0.5px;
    line-height: 1.05;
  }
  .card--front .brand-name {
    position: absolute; left: 30px; top: 122px; width: 240px; font-size: 24px;
  }
  .divider {
    position: absolute; left: 292px; top: 128px; width: 1px; height: 50px; background: var(--rule);
  }
  .address {
    position: absolute; left: 306px; top: 132px;
    font-size: 11px; color: var(--muted); line-height: 1.55;
  }
  .contacts {
    position: absolute; left: 30px; bottom: 26px; list-style: none;
    font-size: 12px; color: var(--ink); line-height: 1.6;
  }
  .contacts li { display: flex; align-items: center; gap: 7px; }
  .contacts svg { width: 11px; height: 11px; flex: none; }

  .card--back .brand-name {
    position: absolute; left: 0; right: 0; top: 108px; text-align: center; font-size: 30px;
  }
  .web {
    position: absolute; left: 0; right: 0; top: 200px; text-align: center;
    font-size: 16px; color: var(--ink); letter-spacing: 1px;
  }
</style>
</head>
<body>
<main class="canvas">
  <section class="card card--front" aria-label="Card front">
    <svg class="corner-bands" viewBox="0 0 525 110" aria-hidden="true">
      <polygon points="180,0 525,0 525,32 180,60" fill="var(--forest)"/>
      <polygon points="180,60 525,32 525,78 420,78 300,78" fill="var(--maroon)"/>
      <path d="M430 78 Q445 48 480 46 L525 46 L525 78 Z" fill="var(--card)"/>
      <polygon points="180,60 420,78 180,78" fill="var(--card)"/>
    </svg>
    <div class="holder">
      <p class="holder__name">Your Name</p>
      <p class="holder__title">Title</p>
    </div>

    <h1 class="brand-name">Silver Harbor Rhythm</h1>
    <div class="divider"></div>
    <p class="address">Sreet Name, City Name<br>Zip Code-00000</p>

    <ul class="contacts">
      <li>
        <svg viewBox="0 0 12 12" aria-hidden="true"><circle cx="6" cy="6" r="6" fill="var(--forest)"/><path d="M4 3.2 L5 4.6 L4.5 5.3 Q5.3 6.8 6.7 7.5 L7.4 7 L8.8 8 L8.2 9 Q5 8.8 3.1 4.1 Z" fill="#fff"/></svg>
        <span>555 274 9160</span>
      </li>
      <li>
        <svg viewBox="0 0 12 12" aria-hidden="true"><circle cx="6" cy="6" r="6" fill="var(--forest)"/><rect x="3" y="4" width="6" height="4.2" fill="#fff"/><path d="M3 4 L6 6.4 L9 4" stroke="var(--forest)" stroke-width="0.8" fill="none"/></svg>
        <span>silverharborrhythm@mailnest.net</span>
      </li>
      <li>
        <svg viewBox="0 0 12 12" aria-hidden="true"><circle cx="6" cy="6" r="6" fill="var(--forest)"/><circle cx="6" cy="6" r="3.2" stroke="#fff" stroke-width="0.8" fill="none"/><path d="M2.8 6 H9.2 M6 2.8 V9.2" stroke="#fff" stroke-width="0.7"/></svg>
        <span>www.silverharborrhythm.net</span>
      </li>
    </ul>
  </section>

  <section class="card card--back" aria-label="Card back">
    <h2 class="brand-name">Silver Harbor Rhythm</h2>
    <p class="web">www.silverharborrhythm.net</p>
  </section>
</main>
</body>
</html>
```